Mortgage Specialist Wordpress Build

I have a current WordPress site but I would like a whole new site built using the same domain. I've included a site for reference in my outline. The main focus of the website is to educate and capture leads.
I would like my blogs to stay for SEO already earned. Please see work requested attached.
Updates
Project Deadline Extended Reason: I am extending the deadline because I didn't realize this was a design only and I need the website coded as well. I've purchased the add-on. This is my first time using Pixel Harbor so please bare with me. I have additional Wordpress sites I want to have built too. Thanks, Colin Added Tuesday, April 18, 2017
Target Market(s)
Home Buyers, Home owners looking to refinance or renew their mortgages
Industry/Entity Type
Mortgage
Coding
Coded - Design and coding required
Font styles to use
Look and feel
Each slider illustrates characteristics of the customer's brand and the style your logo design should communicate.

```html
<!DOCTYPE html>
<html lang="en">
<head>
<meta charset="utf-8">
<title>Harborline Lending – Mortgage Specialist</title>
<link href="https://fonts.googleapis.com/css2?family=Nunito+Sans:wght@300;400;600;700&family=Open+Sans:wght@400&display=swap" rel="stylesheet">
<style>
:root{
  --navy:#0b3c80;
  --gold:#f4cd1e;
  --pill:#f8e4a0;
  --strip:#efefef;
  --footer:#ececec;
  --ink:#333;
  --muted:#5a5a5a;
  --white:#fff;
}
*{box-sizing:border-box;margin:0;padding:0}
html,body{width:1200px;height:2459px;overflow:hidden}
body{position:relative;background:var(--white);font-family:"Nunito Sans",Arial,sans-serif;color:var(--ink)}
.abs{position:absolute}

/* Header */
.site-header{left:0;top:0;width:1200px;height:123px;background:var(--navy)}
.brand{left:123px;top:42px;width:200px;text-align:center;color:var(--white);font-size:22px;font-weight:700;letter-spacing:.5px;line-height:1.1}
.brand small{display:block;font-size:22px}
.nav a{position:absolute;top:48px;height:36px;line-height:36px;color:var(--white);font-size:17px;font-weight:600;text-decoration:none;text-align:center;text-transform:uppercase}
.nav .current{left:577px;width:122px;border:2px solid var(--white);line-height:32px}

/* Hero */
.hero{left:0;top:123px;width:1200px;height:563px;background:linear-gradient(180deg,#6b7685 0%,#4d5563 45%,#3b4049 100%)}
.hero-title{left:0;top:372px;width:1194px;text-align:center;color:var(--white);font-size:36px;font-weight:700}
.hero-sub{left:0;top:420px;width:1194px;text-align:center;color:var(--white);font-size:32px;font-weight:300}
.btn{display:block;text-align:center;font-size:18px;font-weight:600;color:var(--white);text-decoration:none}
.btn-solid{left:375px;top:490px;width:210px;height:46px;line-height:46px;background:var(--navy)}
.btn-ghost{left:600px;top:490px;width:206px;height:46px;line-height:44px;border:2px solid var(--white)}

/* Partner strip */
.partners{left:0;top:686px;width:1200px;height:118px;background:var(--strip);border-bottom:1px solid #ddd}
.partner{position:absolute;top:44px;font-size:17px;font-weight:600;color:#444;display:flex;align-items:center;gap:8px}
.partner i{display:inline-block;width:20px;height:20px;background:#555}

/* Help */
.help-title{left:0;top:885px;width:1200px;text-align:center;font-size:36px;font-weight:300;color:#444}
.help-card{width:280px;height:280px;border:3px solid var(--navy);border-radius:50%;background:var(--white);box-shadow:0 22px 18px -14px rgba(0,0,0,.18);text-align:center}
.help-card svg{position:absolute;left:100px;top:55px}
.help-card h3{position:absolute;top:140px;width:100%;font-size:24px;font-weight:400;color:var(--navy)}
.help-card a{position:absolute;left:86px;top:193px;width:108px;height:33px;line-height:33px;border-radius:17px;background:var(--pill);color:#333;font-size:15px;text-decoration:none}

/* Questions band */
.questions{left:0;top:1276px;width:1200px;height:300px;background:var(--gold)}
.questions h2{position:absolute;top:75px;width:100%;text-align:center;color:var(--white);font-size:38px;font-weight:300}
.questions a{position:absolute;left:428px;top:144px;width:336px;height:50px;line-height:50px;border-radius:25px;background:var(--navy);color:var(--white);text-align:center;font-size:19px;text-decoration:none}

/* Bio */
.bio-photo{left:126px;top:1634px;width:333px;height:360px;background:linear-gradient(160deg,#5b5e63,#2c2d30)}
.bio-title{left:489px;top:1632px;font-size:38px;font-weight:300;color:#555}
.bio-text{left:492px;top:1697px;width:590px;font-family:"Open Sans",Arial,sans-serif;font-size:14.1px;line-height:26px;color:var(--muted)}
.bio-text p+p{margin-top:26px}

/* Footer */
.site-footer{left:0;top:2070px;width:1200px;height:321px;background:var(--footer);border-top:1px solid #ddd}
.f-col{top:62px}
.f-col h4{font-size:18px;font-weight:400;color:#333;margin-bottom:12px;text-transform:uppercase}
.f-col li{list-style:none;font-size:16px;line-height:29px;color:#444}
.socials{left:144px;top:233px;display:flex;gap:6px}
.socials span{width:36px;height:36px;border:2px solid #222;border-radius:50%}
.badge{left:915px;top:41px;width:104px;height:104px;border-radius:50%;background:var(--navy);border:5px solid #cfd6e3}
.f-brand{left:857px;top:222px;width:220px;text-align:center;font-size:22px;font-weight:700;color:#222;line-height:1.1}
.copyright{left:0;top:2410px;width:1200px;text-align:center;font-size:14px;color:#555}
</style>
</head>
<body>

<header class="site-header abs">
  <div class="brand abs">Harborline<small>Lending</small></div>
  <nav class="nav">
    <a class="current" href="#">Home</a>
    <a href="#" style="left:721px;width:80px">About</a>
    <a href="#" style="left:846px;width:72px">Blog</a>
    <a href="#" style="left:970px;width:100px">Contact</a>
  </nav>
</header>

<section class="hero abs" role="img" aria-label="Aerial photograph of a downtown city skyline with office towers"></section>
<svg class="abs" style="left:553px;top:274px" width="88" height="88" viewBox="0 0 88 88" aria-hidden="true">
  <circle cx="44" cy="44" r="41" fill="none" stroke="#fff" stroke-width="2.5"/>
  <path d="M36 29 L60 44 L36 59 Z" fill="none" stroke="#fff" stroke-width="2.5" stroke-linejoin="round"/>
</svg>
<h1 class="hero-title abs">Class aptent taciti sociosqu litora torquent</h1>
<p class="hero-sub abs">Aonubia nostra inceptos hymenaeos</p>
<a class="btn btn-solid abs" href="#">Get Hooked Up</a>
<a class="btn btn-ghost abs" href="#">I'm a Client</a>

<section class="partners abs" aria-label="Lending partners">
  <span class="partner" style="left:160px"><i></i>Quenby Savings</span>
  <span class="partner" style="left:345px">Orvel Fund</span>
  <span class="partner" style="left:470px">Tarnwell</span>
  <span class="partner" style="left:580px">Pelmora</span>
  <span class="partner" style="left:680px"><i></i>Brisk Ledger</span>
  <span class="partner" style="left:825px">Lumae Union</span>
  <span class="partner" style="left:960px">Varnholt</span>
</section>

<h2 class="help-title abs">I need help with</h2>

<div class="help-card abs" style="left:139px;top:951px">
  <svg width="80" height="70" viewBox="0 0 80 70" aria-hidden="true" fill="none" stroke="#0b3c80" stroke-width="3.5" stroke-linecap="round" stroke-linejoin="round">
    <path d="M4 6h12l8 36h40l8-26H19"/><path d="M28 24h44M30 33h38"/><circle cx="32" cy="56" r="5"/><circle cx="60" cy="56" r="5"/>
  </svg>
  <h3>Purchase</h3><a href="#">Click here</a>
</div>

<div class="help-card abs" style="left:465px;top:951px">
  <svg width="80" height="76" viewBox="0 0 80 76" aria-hidden="true" fill="none" stroke="#0b3c80" stroke-width="3.5" stroke-linecap="round" stroke-linejoin="round">
    <path d="M18 20a30 30 0 0 1 48 4"/><path d="M62 56a30 30 0 0 1-48-4"/><path d="M68 12v13H55"/><path d="M12 64V51h13"/>
    <path d="M48 28c-2-3-5-4-8-4-5 0-8 3-8 6 0 8 16 5 16 13 0 4-4 6-8 6-4 0-7-2-9-5M40 19v6M40 49v6"/>
  </svg>
  <h3>Refinance</h3><a href="#">Click here</a>
</div>

<div class="help-card abs" style="left:788px;top:951px">
  <svg width="80" height="70" viewBox="0 0 80 70" aria-hidden="true" fill="none" stroke="#0b3c80" stroke-width="4" stroke-linecap="round" stroke-linejoin="round">
    <path d="M12 30c6-16 26-22 42-12l10 6"/><path d="M66 10v15H51"/>
    <path d="M68 40c-6 16-26 22-42 12l-10-6"/><path d="M14 60V45h15"/>
  </svg>
  <h3>Renew</h3><a href="#">Click here</a>
</div>

<section class="questions abs" role="img" aria-label="Yellow-toned photograph of a family in a living room">
  <h2>Real Estate Questions?</h2>
  <a href="#">ASK QUESTIONS</a>
</section>

<div class="bio-photo abs" role="img" aria-label="Portrait photograph of the mortgage specialist"></div>
<h2 class="bio-title abs">BIO</h2>
<div class="bio-text abs">
  <p>Purchasing a home, refinancing a mortgage and renewing a mortgage have one thing in common: they can represent an exciting time in an individual's life but they can also be complex. I am dedicated to giving back to the region by helping people save thousands of dollars in interest and prepayment expenses and find solutions that are fitted to your specific situation.</p>
  <p>In addition to getting you a fantastic rate, I ensure that I take enough time for each and every one of my clients to go over every detail in order to see that their mortgage repayment schedule is on track with their financial objectives. It is my mission to help people in this wonderful area get the best Northport mortgage package possible while providing tremendous care and service.</p>
</div>

<footer class="site-footer abs">
  <div class="f-col abs" style="left:144px">
    <h4>Company</h4>
    <ul><li>Home</li><li>About Us</li><li>Blogs</li><li>Testimonials</li></ul>
  </div>
  <div class="f-col abs" style="left:369px">
    <h4>Resources</h4>
    <ul><li>Term of Use</li><li>Apply</li><li>Contact Us</li></ul>
  </div>
  <div class="f-col abs" style="left:576px">
    <h4>Contact Info</h4>
    <ul><li>148 Harbourview Rd.</li><li>Northport, BC V1A 0B2</li><li>E: colin@homeratepath.ca</li><li>P: 604.555.0182</li><li>F: 604.555.0147</li></ul>
  </div>
  <div class="socials abs" aria-label="Social links"><span></span><span></span><span></span><span></span></div>
  <div class="badge abs" role="img" aria-label="Anniversary badge"></div>
  <div class="f-brand abs">Harborline Lending</div>
</footer>

<p class="copyright abs">© 2017 Company Name&nbsp; All right reserved</p>

</body>
</html>
```